DeskHarbor - Coworking website design

DeskHarbor is a new global coworking brand, growing fast and establishing stylish locations and communities that inspire innovation and collaboration all around the world.
The project includes a complete website design, focused on delivering the company’s values and messages, provide information to site visitors and to generate leads.

Please review the attached design brief, for more information.

Target Market(s)

Both men and women. Decision makers in:
Small & medium businesses in various fields, but mainly technology firms (Startups or established brands).
Global enterprises.
Dynamic “new generation” companies.
Press

Number of Pages Required

2 page

Requirements
Must have
• Project Scope & deliverables:
• Concept and design for :
• Home page
• Deliver the values mentioned above.
• Showcase the cities in which the company has locations in.
• Show customer testimonials.
• Provide an interface (form) for booking a tour and/or leaving contact details for more information (two alternatives)
• Coworking location page - Each location is in the coolest part of a different major city, and has its own address, set of amenities (kitchen, fast internet etc,), area information (public transportation accessibility, sites near by, bars and restaurants in walking distance) and pricing for private offices (based on number of people per office). Each location page must have an interface to book a location tour.
• Site Navigation (header & footer) - allow simple navigation between multiple city pages, location pages and homepage. Growth of up to 50 locations in 25 cities.
• The navigation should account for Navigation to additional pages (not commissioned in this project) such as:
• Locations
• Enterprise
• Special promotions
• Blog
• Contact us
• About us
• Note - the site should account for geolocation variable display, showing different content for different locations.
• Deliverables must include all editable graphic files (photoshop or similar), as follows:
• Home page - Desktop view (preferably both)
• Location page - Mobile web view (preferably both)
• Navigation - both options

```html
<!DOCTYPE html>
<html lang="en">
<head>
<meta charset="utf-8">
<title>DeskHarbor – Coworking</title>
<link rel="stylesheet" href="https://fonts.googleapis.com/css2?family=Open+Sans:wght@300;400;600;700&display=swap">
<style>
:root{
  --ink:#222222;
  --text:#555555;
  --dark:#353535;
  --panel:#e3e3e3;
  --line:#c9c9c9;
  --white:#ffffff;
  --field-text:#666666;
  --btn:#5d5d5d;
  --photo-office:#6f6d6a;
  --photo-lounge:#b8a999;
  --map-base:#d9dcd8;
  --avatar:#7a6f66;
  --social:#3d4e6e;
}
*{box-sizing:border-box;margin:0;padding:0}
html,body{width:1200px;height:2539px;overflow:hidden;background:var(--white)}
body{position:relative;font-family:"Open Sans",Arial,sans-serif;color:var(--ink)}
.abs{position:absolute}

.brand{left:132px;top:26px;font-size:54px;font-weight:700;letter-spacing:-1px;color:var(--ink);line-height:1}
.main-nav{left:525px;top:52px;display:flex;gap:27px;font-size:14px;color:var(--ink);white-space:nowrap}
.main-nav a{color:inherit;text-decoration:none}
.main-nav a.current{text-decoration:underline}

.hero-photo{left:132px;top:115px;width:934px;height:463px;background:linear-gradient(160deg,#9a9893 0%,var(--photo-office) 55%,#3e3d3c 100%)}
.hero-arrow{top:330px;width:22px;height:36px;background:rgba(0,0,0,.35);display:flex;align-items:center;justify-content:center}
.hero-band{left:132px;top:578px;width:934px;height:159px;background:var(--dark);text-align:center;color:var(--white)}
.hero-title{margin-top:28px;font-size:24px;font-weight:300;letter-spacing:.5px}
.hero-btn{display:inline-block;margin-top:17px;width:238px;height:51px;border:1.5px solid var(--white);line-height:48px;font-size:16px;font-weight:600;letter-spacing:.3px}

.welcome{left:132px;top:774px;width:934px;text-align:center}
.welcome h2{font-size:34px;font-weight:400;letter-spacing:.5px}
.welcome p{margin-top:6px;font-size:15px;line-height:24px;color:var(--text)}

.values{left:132px;top:958px;width:934px;height:239px;border:1px solid var(--line)}
.values h3{position:absolute;top:30px;width:100%;text-align:center;font-size:24px;font-weight:400}
.value{position:absolute;display:flex;align-items:center;gap:12px;font-size:19.5px;font-weight:600;color:var(--ink);white-space:nowrap}
.value svg{width:16px;height:16px;fill:var(--ink)}

.map{left:132px;top:1251px;width:934px;height:399px;background:linear-gradient(120deg,#d6dad3 0%,var(--map-base) 40%,#cfe0e4 60%,#d9dcd6 100%)}
.find-band{left:132px;top:1650px;width:934px;height:96px;background:var(--dark)}
.find-label{left:110px;top:31px;font-size:20px;letter-spacing:-.2px;color:var(--white);white-space:nowrap}
.find-form{left:462px;top:25px;width:358px;height:46px;border:1.5px solid #9a9a9a;display:flex}
.find-input{flex:1;background:var(--white);font-size:12.5px;color:var(--field-text);padding:14px 20px}
.find-btn{width:64px;background:var(--dark);color:var(--white);font-size:15px;font-weight:600;text-align:center;line-height:43px}

.lounge-photo{left:132px;top:1778px;width:466px;height:335px;background:linear-gradient(150deg,#d8d2c9 0%,var(--photo-lounge) 55%,#6e5e55 100%)}
.testimonials{left:598px;top:1778px;width:468px;height:335px;background:var(--panel)}
.testimonials h2{position:absolute;left:27px;top:36px;font-size:34px;font-weight:400}
.quote{position:absolute;left:27px;top:94px;width:418px;font-size:14.5px;line-height:24px;color:var(--text)}
.avatar{position:absolute;left:29px;top:245px;width:47px;height:47px;background:linear-gradient(#a59a90,var(--avatar))}
.author{position:absolute;left:90px;top:257px;font-size:15px}
.pager{position:absolute;top:257px;width:22px;height:22px;border:1px solid #888;background:#f3f3f3;display:flex;align-items:center;justify-content:center}

.booking{left:132px;top:2150px;width:934px;height:296px;background:var(--dark)}
.booking h2{position:absolute;top:38px;width:100%;text-align:center;color:var(--white);font-size:34px;font-weight:400}
.field{position:absolute;height:40px;background:var(--white);font-size:13px;color:var(--field-text);padding:11px 15px}
.submit{position:absolute;left:424px;top:197px;width:86px;height:43px;background:var(--btn);color:var(--white);font-size:14px;font-weight:600;text-align:center;line-height:43px}

.footer-nav{left:132px;top:2465px;font-size:12.5px;color:var(--ink);white-space:nowrap}
.footer-nav span{margin:0 8px}
.copyright{left:132px;top:2490px;font-size:12.5px;color:var(--ink)}
.social{left:942px;top:2480px;display:flex;gap:7px}
.social i{display:block;width:25px;height:25px;border-radius:50%;background:var(--social)}
</style>
</head>
<body>

<div class="abs brand">DeskHarbor</div>
<nav class="abs main-nav">
  <a class="current">Locations</a><a>Enterprise</a><a>Special promotions</a><a>Blog</a><a>Contact us</a><a>About us</a>
</nav>

<div class="abs hero-photo" role="img" aria-label="Photo of a team working together at desks in a bright open-plan coworking office"></div>
<div class="abs hero-arrow" style="left:134px"><svg width="10" height="16" viewBox="0 0 10 16"><path d="M8 1L2 8l6 7" stroke="#fff" stroke-width="1.5" fill="none"/></svg></div>
<div class="abs hero-arrow" style="left:1042px"><svg width="10" height="16" viewBox="0 0 10 16"><path d="M2 1l6 7-6 7" stroke="#fff" stroke-width="1.5" fill="none"/></svg></div>
<div class="abs hero-band">
  <div class="hero-title">MAECENAS VEL TORTOR ACCUMSAN QUAM VARIUS</div>
  <div class="hero-btn">BOOK A LOCATION TOUR</div>
</div>

<section class="abs welcome">
  <h2>WELCOME</h2>
  <p>Aenean facilisis tincidunt lectus, id dictum nisi luctus eget. Vivamus efficitur ex condimentum, malesuada eros eget, feugiat nibh. Sed tellus imperdiet eget gravida sit amet, volutpat eget turpis. In nec ultricies est. Etiam mattis augue vehicula odio posuere, sit amet tempus lectus luctus. Nulla facilisi. Etiam vel massa elementum, bibendum tellus venenatis, feugiat massa. Curabitur venenatis lacinia ornare. Cras sollici­tudin cursus dui eu placerat.</p>
</section>

<section class="abs values">
  <h3>VALUES</h3>
  <div class="value" style="left:50px;top:92px"><svg viewBox="0 0 16 16"><path d="M8 1a5 5 0 0 0-3 9v2h6v-2a5 5 0 0 0-3-9zm-1.5 12h3v1.5h-3z"/></svg>Inspire collaboration &amp; Innovation</div>
  <div class="value" style="left:50px;top:131px"><svg viewBox="0 0 16 16"><circle cx="12" cy="3.5" r="2.5"/><circle cx="4" cy="8" r="2.5"/><circle cx="12" cy="12.5" r="2.5"/><path d="M4 8l8-4.5M4 8l8 4.5" stroke="#222" stroke-width="1.5"/></svg>Idea sharing</div>
  <div class="value" style="left:50px;top:171px"><svg viewBox="0 0 16 16"><circle cx="5" cy="5" r="2.5"/><circle cx="11" cy="5" r="2.5"/><path d="M0 14c0-4 2-6 5-6s5 2 5 6zM8 14c0-4 1-6 3-6 3 0 5 2 5 6z"/></svg>Be a part of an exclusive club</div>
  <div class="value" style="left:555px;top:92px"><svg viewBox="0 0 16 16"><path d="M8 .5l2.3 5 5.2.5-4 3.6 1.2 5.2L8 12.1l-4.7 2.7 1.2-5.2-4-3.6 5.2-.5z"/></svg>Realize your greatness</div>
  <div class="value" style="left:555px;top:131px"><svg viewBox="0 0 16 16"><path d="M11.5 1.5l3 3L5 14H2v-3z"/></svg>Style and design awareness</div>
</section>

<div class="abs map" role="img" aria-label="City street map showing the river and workplace location pins"></div>
<div class="abs find-band">
  <div class="abs find-label">FIND AWORKPLACE NEAR YOU...</div>
  <div class="abs find-form"><div class="find-input">Enter your zipcode/country</div><div class="find-btn">FIND</div></div>
</div>

<div class="abs lounge-photo" role="img" aria-label="Photo of a colourful coworking lounge with people meeting at tables and bean bags"></div>
<section class="abs testimonials">
  <h2>TESTIMONIALS</h2>
  <p class="quote">" Etiam id imperdiet lectus. Vivamus lacus justo, ultrices nec erat in, euismod iaculis mauris. Vivamus eleifend vitae nulla vel malesuada. In ac malesuada lacus, et consectetur ante. Fusce vitae lectus sit amet mi pulvinar maximus. Aenean plac erat, nibh vel accumsan aliquet, magna. "</p>
  <div class="avatar" role="img" aria-label="Portrait photo of the customer"></div>
  <div class="author">Mark Dale, City</div>
  <div class="pager" style="left:377px"><svg width="8" height="10" viewBox="0 0 8 10"><path d="M6 1L2 5l4 4" stroke="#333" fill="none" stroke-width="1.3"/></svg></div>
  <div class="pager" style="left:407px"><svg width="8" height="10" viewBox="0 0 8 10"><path d="M2 1l4 4-4 4" stroke="#333" fill="none" stroke-width="1.3"/></svg></div>
</section>

<section class="abs booking">
  <h2>BOOKING A TOUR</h2>
  <div class="field" style="left:17px;top:94px;width:215px">Name</div>
  <div class="field" style="left:245px;top:94px;width:216px">Email</div>
  <div class="field" style="left:473px;top:94px;width:216px">Phone</div>
  <div class="field" style="left:703px;top:94px;width:214px">City</div>
  <div class="field" style="left:17px;top:148px;width:900px">Message</div>
  <div class="submit">SUBMIT</div>
</section>

<div class="abs footer-nav">Locations<span>|</span>Enterprise<span>|</span>Special promotions<span>|</span>Blog<span>|</span>Contact us<span>|</span>About us</div>
<div class="abs copyright">Copyright © 2017 DeskHarbor. &nbsp;All rights reserved.</div>
<div class="abs social" aria-label="Social links"><i></i><i></i><i></i><i></i></div>

</body>
</html>
```